Cleaning Service Company In need of Good Web presence.

The company is a cleaning service company which provides professional staff and service for cleaning. This is a project to build a site that is both solid and a strong recognition of our organization. It is supposed to show quality, cleanliness, professionalism. The use of images and art for imagery is all good just to have a site that is consistent and solid. There might be a chance to make stationary, logo and business cars if someone feels they can build a brand that is consistent. The image we are going for is clean solid and to stand out. Finally stationary should not be expensive to print.

Current logo is attached and can be used or can be made more creative.

Target Market(s)

Corporate and Government entities, that will feel that this company has a brand that sets it apart from the rest. The company is new so the modification of the logo will not be an issue if a more solid brand come out of this project. The idea is to have a clean consistent product that stands our from others in terms of website, stationary, etc

Industry/Entity Type

Cleaning Service

Contact Information for Business Card

P.O.Box 51947
Riffa
Kingdom of Bahrain

Logo Text

Harbor Lane Services

Number of Pages Required

4 page

Font styles to use
Sans Serif

Colors
abd036
cadf82
eaf2ce
9bcb3b

Requirements
Must have
• Green Color to be used in order to stick to the name. Also the creativity and boldness in an elegant manner.
Nice to have
• Arabic name of company
• هاربر لين سرفسس ذ.م.م
• if cannot be put at least make a location should be chosen
• Also could be a bit of 3D given to the logo if it could stay elegent.
Should not have
• Should not show people cleaning.

```html
<!DOCTYPE html>
<html lang="en">
<head>
<meta charset="utf-8">
<title>Harbor Lane Services W.L.L</title>
<link href="https://fonts.googleapis.com/css2?family=Roboto:wght@300;400;500;700&family=Roboto+Slab:wght@300;400;700&display=block" rel="stylesheet">
<style>
:root{
  --green-dark:#0d6b3d;
  --green-top:#0b5e33;
  --green-main:#9bcb3b;
  --green-bright:#abd036;
  --green-soft:#cadf82;
  --green-pale:#eaf2ce;
  --green-olive:#4c8a1a;
  --ink:#2b2b2b;
  --grey-text:#666;
  --paper:#f4f4f1;
  --white:#fff;
  --slab:"Roboto Slab","Rockwell","Zilla Slab","Courier New",serif;
  --sans:"Roboto",Arial,sans-serif;
}
*{margin:0;padding:0;box-sizing:border-box}
html,body{width:1200px;height:2192px;overflow:hidden}
body{position:relative;background:var(--white);font-family:var(--sans);color:var(--ink)}
.abs{position:absolute}

/* top bar */
.topbar{left:0;top:0;width:1200px;height:26px;background:var(--green-top);color:var(--white);font-size:13px}
.topbar .company{position:absolute;left:161px;top:6px;font-weight:500}
.topbar .contacts{position:absolute;right:162px;top:6px;display:flex;gap:16px;align-items:center}
.topbar .contacts span{display:flex;align-items:center;gap:5px}

/* header */
.header{left:0;top:26px;width:1200px;height:85px;background:#f2f2f2}
.nav-band{left:322px;top:26px;width:878px;height:85px;background:var(--green-main);clip-path:polygon(34px 0,100% 0,100% 100%,0 100%)}
.brand{left:161px;top:44px;display:flex;align-items:center;gap:8px;width:150px}
.brand .dot{width:46px;height:46px;border-radius:50%;background:var(--green-dark);flex:none}
.brand .name{font-size:14px;font-weight:700;color:var(--green-dark);line-height:1.2}
.nav{left:372px;top:60px;display:flex;color:var(--white);font-size:14px}
.nav a{color:inherit;text-decoration:none;margin-right:50px}

/* hero */
.hero{left:44px;top:129px;width:1109px;height:491px;border:2px solid var(--green-soft);
  background:linear-gradient(180deg,#8a9eae 0%,#b5c0c4 22%,#6f7f86 45%,#4e5a58 70%,#3d4a2e 100%)}
.hero-copy{left:44px;top:305px;width:1109px;text-align:center;color:var(--white)}
.hero-copy .kicker{font-family:var(--slab);font-weight:300;font-size:24px;letter-spacing:.5px}
.hero-copy h1{font-family:var(--slab);font-weight:700;font-size:35px}
.hero-copy p{font-size:14px;margin-top:4px}
.btn-call{left:538px;top:421px;width:123px;height:36px;border-radius:18px;background:var(--green-bright);border:2px solid var(--green-pale);color:var(--green-dark);font-family:var(--slab);font-size:14px;display:flex;align-items:center;justify-content:center;gap:6px}
.arrow{top:340px;width:40px;height:40px;border-radius:50%;background:rgba(255,255,255,.55);display:flex;align-items:center;justify-content:center}

/* welcome */
.welcome{left:161px;top:655px;width:230px}
.welcome h2{font-family:var(--slab);font-weight:700;font-size:29px;color:#1a1a1a;letter-spacing:-.8px}
.welcome .sub{font-size:12px;letter-spacing:2.5px;color:var(--grey-text);margin-top:2px}
.welcome p{font-size:11px;line-height:19px;color:#777;margin-top:20px}
.btn-outline{left:161px;top:833px;width:137px;height:37px;border:2px solid var(--green-olive);border-radius:19px;display:flex;align-items:center;justify-content:center;font-size:15px;color:var(--green-olive)}
.leaf-spot{border-radius:50%}

/* why choose */
.why{left:402px;top:589px;width:634px;height:281px;background:var(--green-dark);color:var(--white)}
.why h2{position:absolute;left:0;top:36px;width:100%;text-align:center;font-family:var(--slab);font-weight:700;font-size:28px}
.why .rule{position:absolute;top:54px;height:1px;background:var(--green-soft);width:152px}
.feature{position:absolute;top:96px;width:180px;text-align:center}
.feature h3{font-family:var(--slab);font-size:16px;font-weight:700;margin-top:12px}
.feature p{font-size:9.5px;line-height:14.5px;margin-top:6px;padding:0 6px}
.feature .more{font-family:var(--slab);font-weight:700;font-size:13px;margin-top:14px}

/* cleaning services */
.services-band{left:0;top:903px;width:1200px;height:535px;background:radial-gradient(ellipse at 50% 40%,#b8d94f 0%,var(--green-bright) 60%,#9fc62f 100%)}
.section-title{width:1200px;left:0;text-align:center}
.section-title h2{font-family:var(--slab);font-weight:700;font-size:38px;color:#333;letter-spacing:-.3px}
.section-title .sub{font-size:16px;color:#2f3d10;margin-top:2px}
.card{top:1092px;width:277px;height:405px}
.card .photo{width:100%;height:187px;border:1px solid rgba(255,255,255,.7)}
.card h3{font-family:var(--slab);font-weight:400;font-size:19px;text-align:center;margin-top:31px}
.card p{font-size:10.5px;line-height:14.8px;text-align:center;padding:0 17px;margin-top:14px}
.card.dark{background:var(--green-dark);color:var(--white)}
.card.light{background:var(--green-soft);color:#1f3b12}
.btn-more{top:1473px;width:121px;height:37px;border-radius:19px;font-family:var(--slab);font-size:14px;display:flex;align-items:center;justify-content:center;gap:6px;border:2px solid var(--green-pale)}
.btn-more.lime{background:var(--green-bright);color:var(--white)}
.btn-more.deep{background:var(--green-dark);color:var(--white)}

/* how it works */
.paper{left:0;top:1438px;width:1200px;height:551px;background:var(--paper)}
.how-intro{left:250px;top:1679px;width:700px;text-align:center;font-size:11px;line-height:16px;color:#666}
.step{top:1740px;width:200px;text-align:center}
.step .ring{width:132px;height:132px;margin:0 auto;border:3px solid var(--green-main);border-radius:50%;background:var(--white);display:flex;align-items:center;justify-content:center}
.step .l1{font-family:var(--slab);font-weight:300;font-size:20px;color:#333;margin-top:17px;line-height:22px}
.step .l2{font-family:var(--slab);font-weight:700;font-size:21px;color:var(--green-main);line-height:24px;letter-spacing:-.5px}

/* contact strip */
.contact-rule{left:0;top:1988px;width:1200px;height:3px;background:var(--green-main)}
.contact{top:2031px;display:flex;gap:12px;align-items:flex-start}
.contact .label{font-size:13px;font-weight:500;color:var(--green-olive);letter-spacing:.3px}
.contact .value{font-size:15px;color:#333;margin-top:5px}
.contact .small{font-size:11px;color:#444;line-height:13px;margin-top:6px;width:210px}

/* footer */
.footer-right{left:0;top:2108px;width:1200px;height:84px;background:#efefef}
.footer-main{left:0;top:2108px;width:880px;height:84px;background:var(--green-olive);clip-path:polygon(0 0,844px 0,880px 100%,0 100%)}
.footer-nav{left:161px;top:2127px;display:flex;color:var(--white);font-size:13px}
.footer-nav a{color:inherit;text-decoration:none}
.copyright{left:161px;top:2168px;color:var(--white);font-size:11px}
.social{top:2135px;width:30px;height:30px;border:2px solid var(--green-main);border-radius:50%}
</style>
</head>
<body>

<!-- top bar -->
<div class="abs topbar">
  <span class="company">Harbor Lane Services W.L.L</span>
  <div class="contacts">
    <span><svg width="11" height="11" viewBox="0 0 24 24"><path fill="#fff" d="M6.6 10.8a15 15 0 006.6 6.6l2.2-2.2c.3-.3.7-.4 1-.2 1.1.4 2.3.6 3.6.6.6 0 1 .4 1 1V20c0 .6-.4 1-1 1A17 17 0 013 4c0-.6.4-1 1-1h3.5c.6 0 1 .4 1 1 0 1.3.2 2.5.6 3.6.1.3 0 .7-.2 1z"/></svg>(000) 000-0000</span>
    <span><svg width="12" height="10" viewBox="0 0 24 18"><rect x="1" y="1" width="22" height="16" fill="#fff"/><path d="M1 1l11 9 11-9" fill="none" stroke="#0b5e33" stroke-width="2"/></svg>info@harborlaneservicesw.l.l.com</span>
    <span><svg width="9" height="12" viewBox="0 0 18 24"><path fill="#fff" d="M9 0a8 8 0 00-8 8c0 6 8 16 8 16s8-10 8-16a8 8 0 00-8-8zm0 11a3 3 0 110-6 3 3 0 010 6z"/></svg>Find us on map</span>
  </div>
</div>

<!-- header -->
<div class="abs header"></div>
<div class="abs nav-band"></div>
<div class="abs brand"><span class="dot"></span><span class="name">Harbor Lane Services</span></div>
<nav class="abs nav">
  <a href="#">Home</a><a href="#">About Us</a><a href="#">Service</a><a href="#">Quotes</a><a href="#">Testimonials</a><a href="#">Payments</a><a href="#">Contact Us</a>
</nav>

<!-- hero -->
<div class="abs hero" role="img" aria-label="Photograph of a harbour city skyline with a tall tower, seen from a green park at dusk"></div>
<div class="abs arrow" style="left:65px"><svg width="20" height="20" viewBox="0 0 20 20"><path d="M13 3L6 10l7 7" fill="none" stroke="#555" stroke-width="3"/></svg></div>
<div class="abs arrow" style="left:1086px"><svg width="20" height="20" viewBox="0 0 20 20"><path d="M7 3l7 7-7 7" fill="none" stroke="#555" stroke-width="3"/></svg></div>
<div class="abs hero-copy">
  <div class="kicker">RELIABLE SERVICE FOR 100%</div>
  <h1>HARBOR LANE SERVICES W.L.L</h1>
  <p>Lorem Ipsum is simply dummy text of the printing and typesetting industry.</p>
</div>
<div class="abs btn-call"><svg width="9" height="10" viewBox="0 0 9 10"><path d="M0 0l9 5-9 5z" fill="#0d6b3d"/></svg>Call Now!</div>

<!-- welcome -->
<div class="abs welcome">
  <h2>WELCOME TO</h2>
  <div class="sub">Harbor Lane Services</div>
  <p>Lorem Ipsum is simply dummy text of the printing and typesetting industry. Lorem Ipsum has been the industry's standard dummy text ever since the 1500s...</p>
</div>
<div class="abs leaf-spot" style="left:344px;top:632px;width:30px;height:26px;background:var(--green-main)" role="img" aria-label="Small green leaf ornament"></div>
<div class="abs btn-outline">Details</div>

<!-- why choose us -->
<section class="abs why">
  <span class="rule" style="left:15px"></span>
  <h2>WHY CHOOSE US?</h2>
  <span class="rule" style="right:15px"></span>

  <div class="feature" style="left:20px">
    <svg width="40" height="40" viewBox="0 0 40 40"><circle cx="20" cy="18" r="13" fill="none" stroke="#fff" stroke-width="3"/><circle cx="20" cy="18" r="7" fill="#fff"/><path d="M12 29l-3 9 6-3 3 5 2-9M28 29l3 9-6-3-3 5-2-9" fill="#fff"/></svg>
    <h3>QUALITY</h3>
    <p>Lorem Ipsum is simply dummy text of the printing and typesetting industry. Lorem Ipsum has been...</p>
    <div class="more">Read More!</div>
  </div>
  <div class="feature" style="left:229px">
    <svg width="44" height="52" viewBox="0 0 44 52" style="margin-top:-12px"><rect x="4" y="26" width="16" height="22" fill="none" stroke="#fff" stroke-width="2.5"/><path d="M2 24h20M9 30v14M15 30v14" stroke="#fff" stroke-width="2"/><rect x="28" y="14" width="10" height="22" rx="2" fill="#fff"/><rect x="29" y="36" width="3.5" height="14" fill="#fff"/><rect x="33.5" y="36" width="3.5" height="14" fill="#fff"/><circle cx="33" cy="7" r="5" fill="#fff"/><path d="M28 18l-6 6" stroke="#fff" stroke-width="3"/></svg>
    <h3>CLEANLINESS</h3>
    <p>Lorem Ipsum is simply dummy text of the printing and typesetting industry. Lorem Ipsum has been...</p>
    <div class="more">Read More!</div>
  </div>
  <div class="feature" style="left:432px">
    <svg width="52" height="40" viewBox="0 0 52 40"><path d="M2 14l10-6 10 4 8-4 10 2 10 6-8 14-12 6-10-4-10-8z" fill="none" stroke="#fff" stroke-width="3" stroke-linejoin="round"/><path d="M20 14l8 6 6-2M18 24l6 4M22 20l8 6" stroke="#fff" stroke-width="2.5" fill="none"/></svg>
    <h3>PROFESSIONALISM</h3>
    <p>Lorem Ipsum is simply dummy text of the printing and typesetting industry. Lorem Ipsum has been...</p>
    <div class="more">Read More!</div>
  </div>
</section>

<!-- cleaning services -->
<div class="abs services-band"></div>
<svg class="abs" style="left:360px;top:950px" width="480" height="90" viewBox="0 0 480 90" aria-hidden="true">
  <g stroke="#fff" stroke-width="1.5"><path d="M52 28v54M4 58h44M428 28v54M432 58h44"/></g>
</svg>
<div class="abs leaf-spot" style="left:382px;top:954px;width:30px;height:24px;background:var(--green-dark)" role="img" aria-label="Green leaf ornament"></div>
<div class="abs leaf-spot" style="left:788px;top:954px;width:30px;height:24px;background:var(--green-dark)" role="img" aria-label="Green leaf ornament"></div>
<div class="abs section-title" style="top:972px">
  <h2>Cleaning Services</h2>
  <div class="sub">Harbor Lane Services W.L.L</div>
</div>

<article class="abs card dark" style="left:161px">
  <div class="photo" role="img" aria-label="Photo of a bucket with cleaning spray bottles, brushes and cloths" style="background:linear-gradient(135deg,#e8eef2 0%,#9ab0c0 45%,#d9b935 70%,#eef2f4 100%)"></div>
  <h3>RESIDENTIAL CLEANING</h3>
  <p>Lorem Ipsum is simply dummy text of the printing and typesetting industry. Lorem Ipsum has been the industry's standard dummy text ever since the 1500s, when an unknown printer took a galley of type and scrambled it to make...</p>
</article>
<article class="abs card light" style="left:460px">
  <div class="photo" role="img" aria-label="Photo of a glass office tower against a blue sky" style="background:linear-gradient(180deg,#3f6fb0 0%,#7fa6d6 45%,#2f4a6e 100%)"></div>
  <h3>COMMERCIAL CLEANING</h3>
  <p>Lorem Ipsum is simply dummy text of the printing and typesetting industry. Lorem Ipsum has been the industry's standard dummy text ever since the 1500s, when an unknown printer took a galley of type and scrambled it to make...</p>
</article>
<article class="abs card dark" style="left:763px">
  <div class="photo" role="img" aria-label="Photo of natural cleaners: a vinegar bottle, baking soda bowl and lemon halves" style="background:linear-gradient(135deg,#c9d835 0%,#e6e9c4 40%,#f0c23a 70%,#b8cc2e 100%)"></div>
  <h3>GREEN CLEANING</h3>
  <p>Lorem Ipsum is simply dummy text of the printing and typesetting industry. Lorem Ipsum has been the industry's standard dummy text ever since the 1500s, when an unknown printer took a galley of type and scrambled it to make...</p>
</article>

<!-- how it works -->
<div class="abs paper"></div>
<div class="abs" style="left:161px;top:1438px;width:277px;height:59px;background:var(--green-dark)"></div>
<div class="abs" style="left:460px;top:1438px;width:277px;height:59px;background:var(--green-soft)"></div>
<div class="abs" style="left:763px;top:1438px;width:277px;height:59px;background:var(--green-dark)"></div>
<div class="abs btn-more lime" style="left:239px"><svg width="9" height="10" viewBox="0 0 9 10"><path d="M0 0l9 5-9 5z" fill="#fff"/></svg>More Info</div>
<div class="abs btn-more deep" style="left:539px"><svg width="9" height="10" viewBox="0 0 9 10"><path d="M0 0l9 5-9 5z" fill="#fff"/></svg>More Info</div>
<div class="abs btn-more lime" style="left:840px"><svg width="9" height="10" viewBox="0 0 9 10"><path d="M0 0l9 5-9 5z" fill="#fff"/></svg>More Info</div>

<svg class="abs" style="left:405px;top:1568px" width="390" height="80" viewBox="0 0 390 80" aria-hidden="true">
  <g stroke="#9bcb3b" stroke-width="1.5"><path d="M52 26v50M4 54h44M338 26v50M342 54h44"/></g>
</svg>
<div class="abs leaf-spot" style="left:425px;top:1572px;width:28px;height:22px;background:var(--green-main)" role="img" aria-label="Green leaf ornament"></div>
<div class="abs leaf-spot" style="left:744px;top:1572px;width:28px;height:22px;background:var(--green-main)" role="img" aria-label="Green leaf ornament"></div>
<div class="abs section-title" style="top:1598px"><h2>How it Works</h2></div>
<p class="abs how-intro">Lorem Ipsum is simply dummy text of the printing and typesetting industry. Lorem Ipsum has been the industry's standard dummy text ever since the 1500s, when an unknown printer took a galley of type and scrambled it to make...</p>

<div class="abs step" style="left:138px">
  <div class="ring"><svg width="64" height="54" viewBox="0 0 64 54"><path d="M4 6l16 16M6 22L22 6" stroke="#0d6b3d" stroke-width="5" stroke-linecap="round"/><rect x="26" y="18" width="34" height="30" rx="2" fill="#0d6b3d"/><path d="M31 27l3 3 5-5M31 38l3 3 5-5" stroke="#fff" stroke-width="2" fill="none"/><path d="M43 28h12M43 39h12" stroke="#fff" stroke-width="2"/></svg></div>
  <div class="l1">Submit your</div><div class="l2">service request</div>
</div>
<div class="abs step" style="left:397px">
  <div class="ring"><svg width="56" height="66" viewBox="0 0 56 66"><path d="M16 40l-8 22 10-5 6 8 4-18M40 40l8 22-10-5-6 8-4-18" fill="#0d6b3d"/><path d="M28 2l6 5 8-1 2 8 7 4-3 7 3 7-7 4-2 8-8-1-6 5-6-5-8 1-2-8-7-4 3-7-3-7 7-4 2-8 8 1z" fill="#0d6b3d"/><circle cx="28" cy="25" r="11" fill="none" stroke="#fff" stroke-width="2"/><path d="M22 25l4 4 8-8" stroke="#fff" stroke-width="3" fill="none"/></svg></div>
  <div class="l1">A certified</div><div class="l2">service technician</div>
</div>
<div class="abs step" style="left:651px">
  <div class="ring"><svg width="38" height="38" viewBox="0 0 38 38"><rect x="2" y="6" width="34" height="30" rx="3" fill="none" stroke="#0d6b3d" stroke-width="3"/><rect x="2" y="6" width="34" height="8" fill="#0d6b3d"/><path d="M10 2v8M28 2v8" stroke="#0d6b3d" stroke-width="3"/><g fill="#0d6b3d"><rect x="8" y="18" width="5" height="4"/><rect x="16.5" y="18" width="5" height="4"/><rect x="25" y="18" width="5" height="4"/><rect x="8" y="26" width="5" height="4"/><rect x="16.5" y="26" width="5" height="4"/><rect x="25" y="26" width="5" height="4"/></g></svg></div>
  <div class="l1">Reach out</div><div class="l2">to you shortly</div>
</div>
<div class="abs step" style="left:870px">
  <div class="ring"><svg width="58" height="58" viewBox="0 0 58 58"><circle cx="29" cy="29" r="26" fill="none" stroke="#0d6b3d" stroke-width="4"/><path d="M29 12v17l-9 8" stroke="#0d6b3d" stroke-width="3" fill="none" stroke-linecap="round"/><g fill="#0d6b3d"><circle cx="29" cy="8" r="1.6"/><circle cx="29" cy="50" r="1.6"/><circle cx="8" cy="29" r="1.6"/><circle cx="50" cy="29" r="1.6"/></g></svg></div>
  <div class="l1">Show Up</div><div class="l2">On Time</div>
</div>

<!-- contact strip -->
<div class="abs contact-rule"></div>
<div class="abs contact" style="left:161px">
  <svg width="50" height="46" viewBox="0 0 50 46"><path d="M4 14c0-6 10-10 21-10s21 4 21 10v4h-10v-4H14v4H4z" fill="none" stroke="#9bcb3b" stroke-width="2.5"/><path d="M10 20h30l4 22H6z" fill="none" stroke="#9bcb3b" stroke-width="2.5"/><circle cx="25" cy="31" r="6" fill="none" stroke="#9bcb3b" stroke-width="2.5"/></svg>
  <div><div class="label">MAKE AN APPOINTMENT</div><div class="value">(000) 000-0000</div></div>
</div>
<div class="abs contact" style="left:460px">
  <svg width="58" height="44" viewBox="0 0 58 44"><path d="M2 16L29 2l27 14v26H2z" fill="none" stroke="#9bcb3b" stroke-width="2.5" stroke-linejoin="round"/><path d="M2 16l27 16 27-16M2 42l20-14M56 42L36 28" fill="none" stroke="#9bcb3b" stroke-width="2.5"/></svg>
  <div><div class="label">EMAIL</div><div class="value">info@harborlaneservicesw.l.l.com</div></div>
</div>
<div class="abs contact" style="left:782px">
  <svg width="36" height="50" viewBox="0 0 36 50"><path d="M18 2a15 15 0 00-15 15c0 12 15 30 15 30s15-18 15-30A15 15 0 0018 2z" fill="none" stroke="#9bcb3b" stroke-width="2.5"/><circle cx="18" cy="17" r="6" fill="none" stroke="#9bcb3b" stroke-width="2.5"/></svg>
  <div><div class="label">VISIT US</div><div class="small">Lorem Ipsum is simply dummy text of the printing and typesetting industry.</div></div>
</div>

<!-- footer -->
<div class="abs footer-right"></div>
<footer class="abs footer-main"></footer>
<nav class="abs footer-nav">
  <a href="#" style="width:82px">Home</a><a href="#" style="width:89px">About Us</a><a href="#" style="width:89px">Service</a><a href="#" style="width:94px">Quotes</a><a href="#" style="width:110px">Testimonials</a><a href="#" style="width:111px">Payments</a><a href="#">Contact Us</a>
</nav>
<div class="abs copyright">Copyright © 2017 Harbor Lane Services W.L.L. All rights reserved.</div>
<div class="abs social" style="left:903px" aria-label="Social profile link"></div>
<div class="abs social" style="left:945px" aria-label="Social profile link"></div>
<div class="abs social" style="left:988px" aria-label="Social profile link"></div>

</body>
</html>
```